Academic and Business book cover

I need a book cover for my academic and business book.
The focus is in international / global negotiation and influence (how to negotiate across cultures).
The book will be published on Zelvorn, both in Vaspet and printed edition. therefore I need something that works under Zelvorn guidelines.The final design should be elegant and still be able to stand out against the competition.
I would like to have orange+grey for the text colors on the cover, even if different options are welcome.
Title and my name are in the attached word doc.

Target Market(s)

graduates, Phds, from international business schools. Managers

Industry/Entity Type

Business

Font styles to use
Serif
Sans Serif

Colors

Designer to choose colors to be used in the design.

Requirements
Must have
• The title and my name should have elegant fonts.
Nice to have
• pictures of the world that don't have the "usual" Europe in the centre.

```html
<!DOCTYPE html>
<html lang="en">
<head>
<meta charset="utf-8">
<title>Strategic Bargaining and Persuasion Methods for Cross-Border Success — Cover</title>
<link href="https://fonts.googleapis.com/css2?family=Arimo:wght@400;700&display=swap" rel="stylesheet">
<style>
  :root {
    --page-bg: #ffffff;
    --cover-bg: #404042;
    --tab-grey: #6d6d70;
    --title-orange: #f2a93b;
    --author-grey: #e2e2e2;
    --rule-green: #b9d9a8;
    --band-olive: #8a9a62;
    --band-slate: #6f84aa;
    --quad-orange: #b86e4e;
    --quad-rose: #b45a72;
    --globe-ocean: #2ba6e0;
    --globe-land: #1f9a4c;
  }
  html, body {
    margin: 0;
    width: 1200px;
    height: 1000px;
    overflow: hidden;
    background: var(--page-bg);
  }
  .book-cover {
    position: absolute;
    left: 302px;
    top: 60px;
    width: 595px;
    height: 880px;
    display: block;
  }
  .cover-ground { fill: var(--cover-bg); }
  .title-tab { fill: var(--tab-grey); }
  .cover-title {
    font-family: "Arimo", Arial, sans-serif;
    font-weight: 700;
    font-size: 18.5px;
    fill: var(--title-orange);
  }
  .cover-author {
    font-family: "Arimo", Arial, sans-serif;
    font-weight: 400;
    font-size: 15.5px;
    fill: var(--author-grey);
  }
  .author-rule { fill: var(--rule-green); }
  .quad-orange { fill: var(--quad-orange); opacity: 0.75; }
  .quad-rose { fill: var(--quad-rose); opacity: 0.75; }
  .globe { opacity: 0.9; }
  .band-vertical { fill: var(--band-olive); opacity: 0.5; }
  .band-vertical-top { fill: var(--band-olive); opacity: 0.75; }
  .band-horizontal { fill: var(--band-slate); opacity: 0.55; }
  .globe-stop-ocean { stop-color: var(--globe-ocean); }
  .globe-stop-land { stop-color: var(--globe-land); }
</style>
</head>
<body>
<svg class="book-cover" viewBox="0 0 460 680" xmlns="http://www.w3.org/2000/svg">
  <defs>
    <linearGradient id="globe-fill" x1="0" y1="0" x2="1" y2="1">
      <stop offset="0" class="globe-stop-land"/>
      <stop offset="0.5" class="globe-stop-ocean"/>
      <stop offset="1" class="globe-stop-land"/>
    </linearGradient>
  </defs>

  <rect class="cover-ground" x="0" y="0" width="460" height="680"/>

  <rect class="title-tab" x="0" y="124" width="38" height="57"/>
  <rect class="title-tab" x="422" y="124" width="38" height="57"/>

  <text class="cover-title" text-anchor="middle">
    <tspan x="230" y="146">Strategic Bargaining and Persuasion</tspan>
    <tspan x="230" y="171">Methods for Cross-Border Success</tspan>
  </text>

  <text class="cover-author" x="230" y="207" text-anchor="middle">Miriam T. Okafor</text>
  <rect class="author-rule" x="159" y="222" width="142" height="2"/>

  <rect class="quad-orange" x="88" y="288" width="145" height="164"/>
  <rect class="quad-rose" x="233" y="288" width="145" height="164"/>
  <rect class="quad-rose" x="88" y="452" width="145" height="165"/>
  <rect class="quad-orange" x="233" y="452" width="145" height="165"/>

  <circle class="globe" cx="232" cy="473" r="145" fill="url(#globe-fill)"
          role="img" aria-label="Globe showing the Americas at the centre"/>

  <rect class="band-vertical-top" x="159" y="224" width="142" height="64"/>
  <rect class="band-vertical" x="159" y="288" width="142" height="329"/>
  <rect class="band-vertical-top" x="159" y="617" width="142" height="63"/>

  <rect class="band-horizontal" x="0" y="392" width="460" height="126"/>
</svg>
</body>
</html>
```